1/2 page ad, 1/2 HORIZONTAL 9.875" x 5", for magazine

We need an ad design that tastefully describes the services we offer.

The Meadowlark Heritage Centre is the heart of Vancouver. We provide classic, updated banquet halls with integrated audio visual capabilities and soaring ceilings. With nine rental halls we are home for international conferences, intimate family gatherings and celebrations for up to 1400 people. Our central location, free parking and full service catering are an ideal solution for weddings, celebrations of life and Christmas parties. With break out rooms and separate rooms for dining and meeting, we are a tremendous asset for the Vancouver destination conferences, awards nights and ceremonies.

1. A PDF x/1a file (CMYK, all fonts embedded, images 200ppi) Black or grey recommended
% of black only.
2. An Illustrator CS6 (or lower) file or eps file with all fonts converted to outlines and all
images embedded. Colour space must be CMYK, not RGB. Images should be 200ppi

```html
<!DOCTYPE html>
<html lang="en">
<head>
<meta charset="utf-8">
<title>Meadowlark Heritage Centre – Services Ad</title>
<link href="https://fonts.googleapis.com/css2?family=Lilita+One&family=Poppins:ital,wght@0,400;0,500;0,600;0,700;1,400;1,600;1,700&display=swap" rel="stylesheet">
<style>
  :root{
    --page:#dcdddf;
    --red:#e31e26;
    --blue:#2e3192;
    --white:#ffffff;
    --brown:#7a4b36;
    --rule:#e2dcd8;
    --photo-light:#f3ece3;
    --photo-mid:#d9c3a8;
    --photo-dark:#a9835e;
  }
  *{box-sizing:border-box;margin:0;padding:0}
  html,body{width:939px;height:1200px;overflow:hidden}
  body{background:var(--page);font-family:"Poppins",sans-serif;position:relative}
  .ad{position:absolute;left:20px;top:372px;width:900px;height:456px;background:var(--white);overflow:hidden;box-shadow:0 2px 6px rgba(0,0,0,.15)}
  .hall-photo{position:absolute;left:0;top:0;width:558px;height:268px;
    background:linear-gradient(180deg,var(--photo-mid) 0%,var(--photo-light) 35%,#f7f3ee 55%,var(--photo-mid) 80%,var(--photo-dark) 100%)}
  .services-panel{position:absolute;left:558px;top:0;width:342px;height:246px;background:var(--red);color:var(--white)}
  .services-title{position:absolute;left:0;right:0;top:16px;text-align:center;font-family:"Lilita One",sans-serif;font-size:46px;line-height:44px;letter-spacing:1px}
  .services-sub{position:absolute;left:0;right:0;top:58px;text-align:center;font-family:"Lilita One",sans-serif;font-size:24px;line-height:26px;letter-spacing:1px}
  .services-sub::before,.services-sub::after{content:"";position:absolute;top:13px;width:42px;height:1px;background:var(--white)}
  .services-sub::before{left:66px}
  .services-sub::after{right:44px}
  .service{position:absolute;display:flex;align-items:center;gap:9px;font-weight:600;font-size:14.5px;line-height:14px}
  .service-icon{width:34px;height:34px;border-radius:50%;background:var(--white);display:flex;align-items:center;justify-content:center;flex:none}
  .tagline{position:absolute;left:558px;top:246px;width:342px;height:35px;text-align:center;color:var(--brown);font-size:11.5px;line-height:13px;padding-top:4px;padding-left:20px}
  .tagline em{font-style:italic}
  .tagline strong{font-style:italic;font-weight:700;display:block}
  .culture-panel{position:absolute;left:558px;top:281px;width:342px;height:175px;background:var(--blue);color:var(--white)}
  .culture-label{position:absolute;left:60px;top:16px;width:14px;height:58px;writing-mode:vertical-rl;transform:rotate(180deg);font-weight:700;font-size:9.5px;line-height:9px;text-align:center}
  .culture-list{position:absolute;list-style:none;font-size:10.5px;line-height:12px;white-space:nowrap}
  .culture-list li{position:relative;padding-left:12px;margin-bottom:6px}
  .culture-list li::before{content:"";position:absolute;left:0;top:2px;width:7px;height:7px;background:var(--red);border-radius:1px}
  .culture-list li::after{content:"";position:absolute;left:2px;top:3px;width:2px;height:4px;border:solid var(--white);border-width:0 1.2px 1.2px 0;transform:rotate(40deg)}
  .phone-pill{position:absolute;left:80px;top:86px;width:195px;height:27px;border-radius:14px;background:var(--white);display:flex;align-items:center;justify-content:center;gap:6px;color:var(--red);font-family:"Lilita One",sans-serif;font-size:20px;letter-spacing:.5px}
  .contact{position:absolute;font-size:9.5px;line-height:17px;white-space:nowrap}
  .contact div{display:flex;align-items:center;gap:5px}
  .contact .dot{width:11px;height:11px;border-radius:50%;background:var(--red);display:inline-flex;align-items:center;justify-content:center;flex:none}
  .badge{position:absolute;left:504px;top:207px;width:110px;height:110px;border-radius:50%;background:var(--white);border:3px solid var(--white);box-shadow:0 0 0 2px var(--blue) inset;display:flex;align-items:center;justify-content:center;text-align:center;color:var(--blue);font-weight:600;font-size:11px;line-height:13px;padding:14px}
  .copy{position:absolute;color:var(--brown);font-size:11.2px;line-height:13.7px}
  .copy strong{font-weight:700;font-style:italic}
  .col-rule{position:absolute;left:204px;top:288px;width:1px;height:148px;background:var(--rule)}
  .row-rule{position:absolute;left:205px;top:353px;width:295px;height:1px;background:var(--rule)}
  .feature{position:absolute;display:flex;align-items:flex-start;gap:8px;color:var(--brown);font-size:11.2px;line-height:13.5px}
  .feature svg{flex:none}
</style>
</head>
<body>
<main class="ad">
  <div class="hall-photo" role="img" aria-label="Banquet hall with round tables in white linen, gold chairs, floral centrepieces and a draped stage"></div>

  <section class="services-panel">
    <h1 class="services-title">SERVICES</h1>
    <h2 class="services-sub">WE OFFER</h2>

    <div class="service" style="left:58px;top:102px">
      <span class="service-icon"><svg width="22" height="22" viewBox="0 0 22 22" fill="none" stroke="#2e3192" stroke-width="2.2"><circle cx="8" cy="13" r="5.5"/><circle cx="14" cy="11" r="5.5"/><path d="M12 3l2-2 2 2"/></svg></span>Weddings
    </div>
    <div class="service" style="left:184px;top:102px">
      <span class="service-icon"><svg width="22" height="22" viewBox="0 0 22 22" fill="#2e3192"><rect x="2" y="9" width="18" height="9" rx="1"/><rect x="5" y="4" width="5" height="5"/><rect x="12" y="4" width="5" height="5"/><rect x="2" y="19" width="18" height="1.5"/></svg></span>Banquets
    </div>
    <div class="service" style="left:58px;top:149px">
      <span class="service-icon"><svg width="22" height="22" viewBox="0 0 22 22" fill="none" stroke="#2e3192" stroke-width="1.8"><rect x="3" y="4" width="16" height="15" rx="1.5"/><path d="M3 8h16M7 2v4M15 2v4"/><path d="M6 11h2M10 11h2M14 11h2M6 14h2M10 14h2" stroke-width="1.6"/></svg></span>Events
    </div>
    <div class="service" style="left:184px;top:149px">
      <span class="service-icon"><svg width="22" height="22" viewBox="0 0 22 22" fill="none" stroke="#2e3192" stroke-width="2"><circle cx="11" cy="11" r="5"/><circle cx="11" cy="11" r="2.5" fill="#2e3192"/><path d="M2 4v14M20 4v14"/></svg></span>Food
    </div>
    <div class="service" style="left:58px;top:196px">
      <span class="service-icon"><svg width="22" height="22" viewBox="0 0 22 22" fill="none" stroke="#2e3192" stroke-width="1.6"><rect x="4" y="2" width="14" height="18" rx="1"/><rect x="4" y="2" width="14" height="4" fill="#2e3192"/><path d="M4 10h14M4 14h14M9 6v14M13 6v14"/></svg></span>Bingo
    </div>
    <div class="service" style="left:184px;top:196px">
      <span class="service-icon"><svg width="22" height="22" viewBox="0 0 22 22" fill="#2e3192"><path d="M3 3h6l-1 5a2 2 0 0 1-4 0z"/><path d="M13 3h6l-1 5a2 2 0 0 1-4 0z"/><rect x="5.5" y="10" width="1" height="5"/><rect x="15.5" y="10" width="1" height="5"/><path d="M2 16h18v2H2z"/></svg></span>Bar<br>Services
    </div>
  </section>

  <p class="tagline"><em>The Meadowlark Heritage Centre is</em><strong>The heart of Vancouver</strong></p>

  <section class="culture-panel">
    <div class="culture-label">Cultural<br>Services</div>
    <ul class="culture-list" style="left:84px;top:12px">
      <li>Library</li>
      <li>Language Lab</li>
      <li>News,History<br>and culture</li>
    </ul>
    <ul class="culture-list" style="left:177px;top:12px">
      <li>Heritage Classes</li>
      <li>scholarships</li>
      <li>Heritage Societies<br>and Groups</li>
    </ul>
    <div class="phone-pill">
      <svg width="15" height="15" viewBox="0 0 16 16"><circle cx="8" cy="8" r="8" fill="#2e3192"/><path d="M5.5 4.2l1.4-.3.8 2-1 .8a5 5 0 0 0 1.9 2l.8-1 2 .8-.3 1.5c-3 .4-6-2.7-5.6-5.8z" fill="#fff"/></svg>(604) 555-0182
    </div>
    <div class="contact" style="left:22px;top:124px">
      <div><span class="dot"><svg width="6" height="7" viewBox="0 0 6 7"><path d="M3 7L.6 3.5a2.6 2.6 0 1 1 4.8 0z" fill="#fff"/></svg></span>1840 Larkspur Avenue</div>
      <div style="padding-left:16px">Vancouver, B.C V5N 2K7</div>
    </div>
    <div class="contact" style="left:168px;top:124px">
      <div><span class="dot"><svg width="7" height="5" viewBox="0 0 7 5"><rect width="7" height="5" fill="#fff"/><path d="M0 0l3.5 3L7 0" fill="none" stroke="#e31e26" stroke-width=".8"/></svg></span>info@meadowlarkcentre.com</div>
      <div><span class="dot"><svg width="7" height="7" viewBox="0 0 8 8" fill="none" stroke="#fff" stroke-width=".8"><circle cx="4" cy="4" r="3.4"/><path d="M.6 4h6.8M4 .6c-2 2-2 4.8 0 6.8M4 .6c2 2 2 4.8 0 6.8"/></svg></span>www.meadowlarkcentre.com</div>
    </div>
  </section>

  <div class="badge">Meadowlark Heritage Centre</div>

  <p class="copy" style="left:17px;top:291px;width:182px">We provide classic, updated banquet halls with integrated audio visual capabilities and soaring ceilings.</p>
  <p class="copy" style="left:224px;top:291px;width:282px">With break out rooms and separate rooms for dining and meeting, we are a tremendous asset for the Vancouver destination conferences, awards nights and ceremonies.</p>
  <p class="copy" style="left:18px;top:372px;width:182px">With nine rental halls we are home for international conferences, intimate family gatherings and celebrations for <strong>up to 1400 people</strong></p>

  <div class="col-rule"></div>
  <div class="row-rule"></div>

  <div class="feature" style="left:227px;top:364px">
    <svg width="20" height="22" viewBox="0 0 20 22"><path d="M10 1a6 6 0 0 0-6 6c0 4.5 6 10 6 10s6-5.5 6-10a6 6 0 0 0-6-6z" fill="#2e3192"/><circle cx="10" cy="7" r="2.2" fill="#fff"/><ellipse cx="10" cy="19" rx="7" ry="2" fill="none" stroke="#2e3192" stroke-width="1.2"/></svg>
    <span style="padding-top:4px">Our central location</span>
  </div>
  <div class="feature" style="left:386px;top:364px">
    <svg width="20" height="20" viewBox="0 0 20 20"><rect width="20" height="20" rx="3" fill="#2e3192"/><text x="10" y="15" text-anchor="middle" fill="#fff" font-family="Poppins,sans-serif" font-weight="700" font-size="14">P</text></svg>
    <span style="padding-top:4px">Free parking</span>
  </div>
  <div class="feature" style="left:225px;top:394px">
    <svg width="26" height="20" viewBox="0 0 26 20" fill="#2e3192"><rect x="12" y="2" width="2" height="3" rx="1"/><path d="M2 15a11 10 0 0 1 22 0z"/><rect x="0" y="16" width="26" height="2.5" rx="1"/></svg>
    <span>full service catering<br>are an ideal solution<br>for weddings</span>
  </div>
  <div class="feature" style="left:385px;top:394px">
    <svg width="22" height="22" viewBox="0 0 22 22" fill="#2e3192"><path d="M1 21l6-15 9 9z"/><path d="M12 6l3-4M15 8l5-2M16 11l4 1" stroke="#2e3192" stroke-width="1.5" fill="none"/><circle cx="19" cy="3" r="1.2"/><circle cx="11" cy="2" r="1"/></svg>
    <span>celebrations of<br>life and Christmas<br>parties.</span>
  </div>
</main>
</body>
</html>
```